Upstart Retirement Planning Firm needs help with business card design

Harborview Nest Advisors, LLC is looking for help with business card design. We give advice on investments, insurance, and other financial matters related to retirement. There are some required disclosures that we will provide but mostly we are looking for a professional, classy business card that reflects the theme we have chosen. We have a logo that is attached but we would like to add a phrase; "Shaping Your Working Years Into Steady Retirement"

Doubled sided only so that we can add the required disclosures (needed for our industry) on the back of the card. We will provide the exact words for this in 1-2 days.

Target Market(s)

Retirees and Pre-retirees. Professionals 50+ years old

Industry/Entity Type

Financial Planning

Contact Information for Business Card

We currently have two people who will need separate cards so we'd like to have a template so that we can add names for new cards in the future.

For the first run, please show the following information.

Gregor Pelham, MBA, CFP®, AIF®
Financial Advisor, Registered Representative
gpelham@harborviewnest.example
Phone: (555) 318-2946
Toll Free Fax: (800) 555-0193

Address is
2187 Meadowlark Ridge Rd.
Suite K418
Larkfield Bay, ST 23999

Colors
3277b5

Requirements
Must have
• Logo, contact info, small phase to describe business (in description), required legal disclosures on back of the card as follows (in small font)
• Gregor Pelham is a registered representative of and offers securities through Brightmoor Capital Brokerage Corporation, Member FNQX. Brightmoor Capital Brokerage Corporation is a member of the Brightmoor Capital Alliance which is the marketing name for Brightmoor Holding Corporation and its affiliates.
Nice to have
• Rounded edges, raised letters
Should not have
• any colors that aren't in the logo (other than black for font)

```html
<!DOCTYPE html>
<html lang="en">
<head>
<meta charset="utf-8">
<title>Harborview Nest Advisors – Business Card</title>
<link rel="stylesheet" href="https://fonts.googleapis.com/css2?family=Arimo:wght@400;700&display=swap">
<style>
  :root {
    --brand-blue: #3277b5;
    --brand-blue-light: #3d86c6;
    --paper: #ffffff;
    --silver: #c9cbcd;
    --ink: #1e1e1e;
    --backdrop: #e9eaec;
  }
  * { box-sizing: border-box; margin: 0; padding: 0; }
  html, body { width: 1200px; height: 750px; overflow: hidden; }
  body {
    background: var(--backdrop);
    font-family: "Arimo", Arial, sans-serif;
    display: flex;
    align-items: center;
    justify-content: center;
    gap: 50px;
  }
  .card {
    width: 520px;
    height: 297px;
    border-radius: 10px;
    overflow: hidden;
    box-shadow: 0 6px 18px rgba(0,0,0,.18);
    position: relative;
  }

  /* Front */
  .card-front {
    background: linear-gradient(135deg, var(--brand-blue) 0%, var(--brand-blue-light) 100%);
    color: var(--paper);
    display: flex;
    flex-direction: column;
    align-items: center;
    justify-content: center;
    text-align: center;
  }
  .brand-name {
    font-weight: 700;
    font-size: 26px;
    letter-spacing: .5px;
    line-height: 1.2;
    white-space: nowrap;
  }
  .brand-name--light { color: var(--paper); }
  .brand-name--blue { color: var(--brand-blue); font-size: 22px; }
  .brand-rule {
    width: 230px;
    height: 1px;
    background: currentColor;
    margin: 12px auto 0;
    opacity: .8;
  }
  .card-front .brand-rule { color: var(--paper); }
  .tagline {
    margin-top: 44px;
    font-size: 14px;
    letter-spacing: .3px;
    white-space: nowrap;
  }

  /* Back */
  .card-back { background: var(--paper); display: flex; flex-direction: column; }
  .back-brand {
    height: 42%;
    display: flex;
    flex-direction: column;
    align-items: center;
    justify-content: center;
  }
  .back-brand .brand-rule { color: var(--silver); width: 200px; margin-top: 8px; }
  .name-band {
    height: 22%;
    background: var(--brand-blue);
    color: var(--paper);
    display: flex;
    flex-direction: column;
    justify-content: center;
    padding-left: 70px;
  }
  .person-name { font-size: 20px; font-weight: 700; white-space: nowrap; }
  .person-name .credentials { font-size: 12px; }
  .person-title { font-size: 12px; margin-top: 3px; }
  .contact-band {
    flex: 1;
    background: var(--silver);
    color: var(--ink);
    display: flex;
    flex-direction: column;
    justify-content: center;
    align-items: center;
    gap: 5px;
    font-size: 12.5px;
  }
  .contact-row { display: flex; align-items: center; gap: 14px; white-space: nowrap; }
  .contact-item { display: inline-flex; align-items: center; gap: 5px; }
  .icon { width: 13px; height: 13px; fill: var(--brand-blue); flex: none; }
</style>
</head>
<body>

  <section class="card card-front" aria-label="Card front">
    <div class="brand-name brand-name--light">Harborview Nest Advisors, LLC</div>
    <div class="brand-rule"></div>
    <p class="tagline">Shaping Your Working Years Into Steady Retirement</p>
  </section>

  <section class="card card-back" aria-label="Card back">
    <div class="back-brand">
      <div class="brand-name brand-name--blue">Harborview Nest Advisors, LLC</div>
      <div class="brand-rule"></div>
    </div>

    <div class="name-band">
      <p class="person-name">Gregor Pelham, <span class="credentials">MBA, CFP®, AIF®</span></p>
      <p class="person-title">Financial Advisor, Registered Representative</p>
    </div>

    <div class="contact-band">
      <p class="contact-row">2187 Meadowlark Ridge Rd. Suite K418, Larkfield Bay, ST 23999</p>
      <p class="contact-row">
        <span class="contact-item">
          <svg class="icon" viewBox="0 0 24 24" aria-hidden="true"><path d="M6.6 10.8a15.1 15.1 0 0 0 6.6 6.6l2.2-2.2a1 1 0 0 1 1-.25 11.4 11.4 0 0 0 3.6.57 1 1 0 0 1 1 1V20a1 1 0 0 1-1 1A17 17 0 0 1 3 4a1 1 0 0 1 1-1h3.5a1 1 0 0 1 1 1c0 1.25.2 2.45.57 3.57a1 1 0 0 1-.25 1z"/></svg>
          (555) 318-2946
        </span>
        <span class="contact-item">
          <svg class="icon" viewBox="0 0 24 24" aria-hidden="true"><path d="M6.6 10.8a15.1 15.1 0 0 0 6.6 6.6l2.2-2.2a1 1 0 0 1 1-.25 11.4 11.4 0 0 0 3.6.57 1 1 0 0 1 1 1V20a1 1 0 0 1-1 1A17 17 0 0 1 3 4a1 1 0 0 1 1-1h3.5a1 1 0 0 1 1 1c0 1.25.2 2.45.57 3.57a1 1 0 0 1-.25 1z"/></svg>
          (800) 555-0193 (Toll Free)
        </span>
      </p>
      <p class="contact-row">
        <span class="contact-item">
          <svg class="icon" viewBox="0 0 24 24" aria-hidden="true"><path d="M2 5h20v14H2z"/><path d="M3 6l9 7 9-7" fill="none" stroke="#c9cbcd" stroke-width="1.6"/></svg>
          gpelham@harborviewnest.example
        </span>
      </p>
    </div>
  </section>

</body>
</html>
```